New Business Card for our Indoor Golf Training Facility

We are looking for designs for a new business card for our indoor golf training facility. Attached is our logo, our logo with our slogan, and here is our elevator pitch (What makes us different from the others) not sure if all the info will fit on one card, maybe you can condense the elevator pitch? here is the info

Elevator Pitch
We work with serious golfers and those that want to be serious golfers…
to make you better, faster, at all phases of the game…
We use the same state-of-the-art technology as professional golfers…
which produces data sets that shows your improvement in real time.
Our facility is available 24/7 to our members, which allows you to improve on your time.

our website: www.birchpinlinks.com

Target Market(s)

Golfers

Font styles to use
Serif
Sans Serif

Colors
ec1f27
f59195
fbd4d5
919191
d3d3d3
1b1b1b

Requirements
Must have
• our logo or our logo with the slogan, elevator pitch (can be condensed or shortened)

```html
<!DOCTYPE html>
<html lang="en">
<head>
<meta charset="utf-8">
<title>Birch Pin Links – Business Card</title>
<link rel="stylesheet" href="https://fonts.googleapis.com/css2?family=Roboto:wght@400;500;700&family=Roboto+Condensed:wght@400;700&display=swap">
<style>
  :root {
    --red: #ec1f27;
    --red-soft: #e8423f;
    --pink: #f59195;
    --blush: #fbd4d5;
    --grey: #919191;
    --grey-light: #d3d3d3;
    --ink: #1b1b1b;
    --paper: #ffffff;
    --backdrop: #ecebea;
  }
  * { box-sizing: border-box; margin: 0; padding: 0; }
  html, body {
    width: 1200px; height: 911px; overflow: hidden;
    background: var(--backdrop);
    font-family: "Roboto", sans-serif;
  }
  .sheet {
    width: 1200px; height: 911px;
    display: flex; align-items: center; justify-content: center; gap: 40px;
  }
  .card {
    position: relative;
    width: 560px; height: 320px;
    background: var(--paper);
    border-radius: 18px;
    overflow: hidden;
    box-shadow: 0 4px 14px rgba(0,0,0,.12);
  }

  /* Front */
  .card-front .band-top {
    position: absolute; top: 0; left: 0; right: 0; height: 26px;
    background: var(--red-soft);
  }
  .card-front .band-bottom {
    position: absolute; bottom: 0; left: 0; right: 0; height: 44px;
    background: var(--red-soft);
    display: flex; align-items: center; justify-content: flex-end;
    padding-right: 60px;
  }
  .website {
    color: var(--paper); font-size: 15px; letter-spacing: 2.5px;
  }
  .brand {
    position: absolute; left: 34px; top: 150px; width: 250px;
  }
  .brand-name {
    display: block;
    color: var(--red); font-weight: 700; font-size: 28px; line-height: 1;
    white-space: nowrap;
  }
  .slogan {
    color: var(--red); font-size: 11px; margin-top: 6px;
  }
  .divider {
    position: absolute; left: 300px; top: 54px; width: 1px; height: 150px;
    background: var(--grey-light);
  }
  .divider::before {
    content: ""; position: absolute; left: -2px; top: 0; width: 5px; height: 40px;
    background: var(--red);
  }
  .contact {
    position: absolute; left: 322px; top: 56px; color: var(--ink);
  }
  .contact-name { color: var(--red); font-weight: 700; font-size: 22px; line-height: 1.1; }
  .contact-role { font-weight: 500; font-size: 13px; margin-bottom: 8px; }
  .contact-line { font-size: 12px; color: #444; line-height: 1.55; display: flex; align-items: center; gap: 6px; }
  .contact-line svg { width: 11px; height: 11px; fill: var(--red); flex: none; }
  .contact-line.spaced { margin-top: 6px; }

  /* Back */
  .card-back { text-align: center; padding-top: 70px; }
  .title-rule {
    width: 60px; height: 3px; margin: 0 auto; background: var(--red);
  }
  .pitch-title {
    color: var(--red); font-family: "Roboto Condensed", sans-serif;
    font-weight: 700; font-size: 18px; margin: 12px 0 8px;
  }
  .pitch {
    font-family: "Roboto Condensed", sans-serif;
    color: #555; font-size: 12.5px; line-height: 1.55;
  }
  .social { display: flex; justify-content: center; gap: 5px; margin-top: 10px; }
  .social span { width: 14px; height: 14px; border-radius: 50%; background: var(--red); }
</style>
</head>
<body>
<main class="sheet">
  <section class="card card-front">
    <div class="band-top"></div>
    <div class="brand">
      <span class="brand-name">Birch Pin Links</span>
      <p class="slogan">Train Smarter. Play Sharper. Every Day.</p>
    </div>
    <div class="divider"></div>
    <div class="contact">
      <p class="contact-name">Daniel Reyes</p>
      <p class="contact-role">CEO/Founder</p>
      <p class="contact-line">418 W. Alder Lane Suite B4</p>
      <p class="contact-line">Millbrook, OH 45099</p>
      <p class="contact-line spaced">
        <svg viewBox="0 0 24 24"><path d="M6.6 10.8a15 15 0 0 0 6.6 6.6l2.2-2.2c.3-.3.7-.4 1-.2 1.1.4 2.3.6 3.6.6.6 0 1 .4 1 1V20c0 .6-.4 1-1 1A17 17 0 0 1 3 4c0-.6.4-1 1-1h3.5c.6 0 1 .4 1 1 0 1.3.2 2.5.6 3.6.1.3 0 .7-.2 1z"/></svg>
        555-201-3380
      </p>
      <p class="contact-line">
        <svg viewBox="0 0 24 24"><path d="M2 5h20v14H2z M2 5l10 8 10-8" fill="none" stroke="#ec1f27" stroke-width="2.4"/></svg>
        hello@birchpinlinks.com
      </p>
    </div>
    <div class="band-bottom"><span class="website">www.birchpinlinks.com</span></div>
  </section>

  <section class="card card-back">
    <div class="title-rule"></div>
    <h2 class="pitch-title">ELEVATOR PITCH:</h2>
    <p class="pitch">
      We work with serious golfers and those that want to be serious golfers...<br>
      to make you better, faster, at all phases of the game...<br>
      We use the same state-of-the-art technology as professional golfers...<br>
      which produces data sets that shows your improvement in real time.<br>
      Our facility is available 24/7 to our members, which allows you to improve on your time.
    </p>
    <div class="social"><span></span><span></span></div>
  </section>
</main>
</body>
</html>
```